Northfield Builders Guild Business card

We are looking for a new business card design with photo included.
Our business is a nonprofit construction contractor membership organization. We offer business education, assist with business setup and licensing, provide safety training, and provide a member directory.
URL: www.builderslinkguild.org
Color code:
CMYK: 0 cyan, 42 magenta, 100 yellow, 0 black for Print.
Hexidecimal: #FF9900
RGB: R 255; G 153; B 0

```html
<!DOCTYPE html>
<html lang="en">
<head>
<meta charset="UTF-8">
<title>Northfield Builders Guild – Business Card</title>
<link href="https://fonts.googleapis.com/css2?family=Open+Sans:wght@400;600;800&display=swap" rel="stylesheet">
<style>
  :root {
    --brand-orange: #ff9900;
    --card-black: #1a1a1a;
    --ink-dark: #2b2b2b;
    --ink-grey: #555555;
    --paper: #ffffff;
    --backdrop: #2a2a2a;
  }
  * { margin: 0; padding: 0; box-sizing: border-box; }
  html, body { width: 1200px; height: 900px; overflow: hidden; }
  body {
    background: var(--backdrop);
    font-family: "Open Sans", Arial, sans-serif;
    position: relative;
  }
  .card {
    position: absolute;
    left: 285px;
    width: 630px;
    height: 360px;
    overflow: hidden;
    box-shadow: 0 10px 30px rgba(0,0,0,.5);
  }
  .card-front { top: 60px; background: var(--paper); }
  .card-back  { top: 480px; background: var(--card-black); }

  .front-wave { position: absolute; left: 0; top: 0; width: 630px; height: 360px; }

  .front-wordmark {
    position: absolute;
    left: 40px; top: 96px;
    width: 250px;
    font-weight: 800;
    font-size: 34px;
    line-height: 1.02;
    color: var(--ink-dark);
    letter-spacing: -0.5px;
    text-transform: uppercase;
  }
  .divider {
    position: absolute;
    left: 310px; top: 62px;
    width: 2px; height: 170px;
    background: var(--brand-orange);
  }
  .contact { position: absolute; left: 330px; top: 62px; color: var(--ink-grey); }
  .contact-name {
    font-weight: 800; font-size: 20px; color: var(--brand-orange);
    text-transform: uppercase; letter-spacing: 0.3px;
  }
  .contact-title { font-size: 14px; font-style: italic; margin-bottom: 10px; }
  .contact-address { font-size: 13.5px; line-height: 1.4; margin-bottom: 8px; }
  .contact-line { display: flex; align-items: center; gap: 7px; font-size: 13.5px; line-height: 1.55; }
  .contact-line svg { width: 12px; height: 12px; flex: none; }

  .back-wordmark {
    position: absolute; left: 0; right: 0; top: 150px;
    text-align: center;
    font-weight: 800; font-size: 38px;
    color: var(--paper);
    text-transform: uppercase; letter-spacing: -0.5px;
  }
</style>
</head>
<body>

<section class="card card-front">
  <svg class="front-wave" viewBox="0 0 630 360" aria-hidden="true">
    <path d="M0,236 C130,248 220,292 320,324 C400,348 470,356 560,362 L0,362 Z" fill="var(--card-black)"/>
    <path d="M0,228 C130,240 220,284 320,316 C400,340 470,350 560,356" fill="none" stroke="var(--brand-orange)" stroke-width="7"/>
  </svg>

  <div class="front-wordmark">Northfield Builders Guild</div>

  <div class="divider"></div>

  <div class="contact">
    <div class="contact-name">Dana Whitlock</div>
    <div class="contact-title">President</div>
    <div class="contact-address">2450 Alder Ridge Rd., Suite #210<br>Millbrook, OR 97088</div>
    <div class="contact-line">
      <svg viewBox="0 0 12 12"><path d="M2.5 1 L4.5 1 L5.2 3.6 L4 4.6 C4.6 6 5.9 7.3 7.4 8 L8.4 6.8 L11 7.5 L11 9.5 C11 10.4 10.3 11 9.5 11 C5 10.6 1.4 7 1 2.5 C1 1.7 1.6 1 2.5 1 Z" fill="var(--brand-orange)"/></svg>
      (555) 014-2290
    </div>
    <div class="contact-line">
      <svg viewBox="0 0 12 12"><rect x="0.5" y="2" width="11" height="8" fill="var(--brand-orange)"/><path d="M0.5 2 L6 6.5 L11.5 2" fill="none" stroke="#fff" stroke-width="1"/></svg>
      hello@nfbguild.org
    </div>
    <div class="contact-line">
      <svg viewBox="0 0 12 12"><circle cx="6" cy="6" r="5.5" fill="var(--brand-orange)"/><ellipse cx="6" cy="6" rx="2.3" ry="5.5" fill="none" stroke="#fff" stroke-width="0.8"/><line x1="0.5" y1="6" x2="11.5" y2="6" stroke="#fff" stroke-width="0.8"/></svg>
      www.builderslinkguild.org
    </div>
  </div>
</section>

<section class="card card-back">
  <div class="back-wordmark">Northfield Builders Guild</div>
</section>

</body>
</html>
```